Consulting company business cards

We have a base design, but would be willing to update. We have a new logo/"tag" that needs to be added. Current business card design is attached for reference into our "style."

Industry/Entity Type

Business

Contact Information for Business Card

Should contain name and title, office number, mobile number if appropriate, e-mail, website, physical address, and company logo.

Font styles to use
Other font styles liked:
• See current card design on KorvandBCard

Colors
0455a3
85acd3
aaaaaa

Requirements
Must have
• Our colors are navy blue, gray, and a lighter blue
Nice to have
• Design that I can easily drop in new names/titles as we hire employees.

```html
<!DOCTYPE html>
<html lang="en">
<head>
<meta charset="utf-8">
<title>Harrow Business Card</title>
<link rel="stylesheet" href="https://fonts.googleapis.com/css2?family=Open+Sans:wght@400;700;800&display=swap">
<style>
  :root {
    --navy: #0b3555;
    --light-blue: #80b0d2;
    --gray: #aaaaaa;
    --ink: #2a2a2a;
    --card-white: #ffffff;
    --card-dark: #2b2b2b;
    --backdrop: #e9e7e3;
  }
  * { box-sizing: border-box; margin: 0; padding: 0; }
  html, body { width: 1200px; height: 900px; overflow: hidden; }
  body {
    background: var(--backdrop);
    font-family: "Open Sans", Arial, sans-serif;
    display: flex; flex-direction: column; align-items: center; justify-content: center;
    gap: 44px;
  }
  .card {
    position: relative;
    width: 600px; height: 343px;
    box-shadow: 0 6px 18px rgba(0,0,0,.18);
    overflow: hidden;
  }
  .card--back { background: var(--card-dark); }
  .card--front { background: var(--card-white); }
  .card__shapes { position: absolute; inset: 0; }

  .logo { position: absolute; display: flex; align-items: center; gap: 10px; }
  .logo__name {
    font-weight: 800; font-size: 54px; letter-spacing: 3px; line-height: 1;
  }
  .logo__tagline {
    font-weight: 400; font-size: 11.5px; letter-spacing: 2.6px; text-transform: uppercase;
    margin-top: 4px;
  }
  .logo__mark { width: 46px; height: 46px; border-radius: 50%; flex: none; }

  .card--back .logo { left: 50%; top: 50%; transform: translate(-50%, -50%); }
  .card--back .logo__name, .card--back .logo__tagline { color: #ffffff; }
  .card--back .logo__mark { background: #ffffff; }

  .card--front .logo { right: 36px; top: 120px; }
  .card--front .logo__name { color: var(--navy); font-size: 44px; }
  .card--front .logo__tagline { color: var(--gray); font-size: 9.5px; letter-spacing: 2.2px; }
  .card--front .logo__mark { background: var(--light-blue); width: 38px; height: 38px; }

  .person { position: absolute; left: 70px; top: 14px; }
  .person__name { color: var(--navy); font-weight: 700; font-size: 19px; line-height: 1.2; }
  .person__title { color: var(--ink); font-size: 12px; }

  .contact { position: absolute; left: 34px; top: 104px; color: var(--ink); font-size: 13.5px; line-height: 1.35; }
  .contact__address { margin-bottom: 8px; }
  .contact__list { list-style: none; }
  .contact__item { display: flex; align-items: center; gap: 8px; }
  .contact__icon { width: 11px; height: 11px; fill: var(--navy); flex: none; }
</style>
</head>
<body>

  <section class="card card--back" aria-label="Card back">
    <div class="logo">
      <div>
        <div class="logo__name">HARROW</div>
        <div class="logo__tagline">A Cloud Consulting Company</div>
      </div>
      <span class="logo__mark"></span>
    </div>
  </section>

  <section class="card card--front" aria-label="Card front">
    <svg class="card__shapes" viewBox="0 0 600 343" aria-hidden="true">
      <polygon points="0,0 22,0 0,30" fill="var(--light-blue)"/>
      <polygon points="30,0 62,0 62,46 0,46" fill="var(--navy)"/>
      <polygon points="0,262 300,262 284,290 0,290" fill="var(--light-blue)"/>
      <polygon points="300,296 600,296 600,343 278,343" fill="var(--navy)"/>
    </svg>

    <div class="person">
      <div class="person__name">Dana Korvand</div>
      <div class="person__title">Office Manager</div>
    </div>

    <div class="contact">
      <p class="contact__address">2391 W 58TH St Fairview<br>Indiana 46190</p>
      <ul class="contact__list">
        <li class="contact__item">
          <svg class="contact__icon" viewBox="0 0 16 16"><path d="M3 1l3 3-2 2c1 2 3 4 5 5l2-2 3 3-2 3C6 14 2 10 1 3z"/></svg>
          555.014.2910
        </li>
        <li class="contact__item">
          <svg class="contact__icon" viewBox="0 0 16 16"><path d="M4 1h8v4H4zM1 6h14v7h-3v2H4v-2H1zM5 10v4h6v-4z"/></svg>
          555.014.2971
        </li>
        <li class="contact__item">
          <svg class="contact__icon" viewBox="0 0 16 16"><path d="M1 3h14v10H1zM2 4l6 5 6-5z" fill-rule="evenodd"/></svg>
          dkorvand@harrowtech.com
        </li>
        <li class="contact__item">
          <svg class="contact__icon" viewBox="0 0 16 16"><circle cx="8" cy="8" r="7"/></svg>
          harrowtech.com
        </li>
      </ul>
    </div>

    <div class="logo">
      <div>
        <div class="logo__name">HARROW</div>
        <div class="logo__tagline">A Cloud Consulting Company</div>
      </div>
      <span class="logo__mark"></span>
    </div>
  </section>

</body>
</html>
```